Social Media App Needs PPT Template

We need a PowerPoint template for a new social media company based in the DC area called "Bold Ledger." We provide an interactive digital platform for executives to share actionable advice. We would like to see designs that use our orange logo color as an accent, but are mainly grey, white, and black. The final design should communicate clean, chic, modern, and professional.

Target Market(s)

Executives

Industry/Entity Type

Information Technology

Font styles to use
Sans Serif

Colors
f78f20
fbe7d2
ffffff
000000
e8e8e8
757575

Requirements
Must have
• My project must have title page and many options for the body of the ppt (graphs, tables, etc). It also needs to be easy to modify. I must have someone who is experienced in creating powerpoint templates.
Nice to have
• It would be nice to have a very modern and clean design that includes the logo on every page, but still leaves a lot of room for the content of the slide
Should not have
• My design project should not look to busy.

```html
<!DOCTYPE html>
<html lang="en">
<head>
<meta charset="utf-8">
<title>Bold Ledger – Content Slide</title>
<link href="https://fonts.googleapis.com/css2?family=Lato:wght@300;400;700&display=swap" rel="stylesheet">
<style>
  :root {
    --orange: #f78f20;
    --orange-deep: #e67e17;
    --orange-soft: #fbe7d2;
    --white: #ffffff;
    --black: #000000;
    --light-grey: #e8e8e8;
    --mid-grey: #757575;
    --stage: #939393;
    --placeholder: #cdced0;
    --body-text: #474747;
  }
  * { margin: 0; padding: 0; box-sizing: border-box; }
  html, body {
    width: 1200px; height: 960px; overflow: hidden;
    background: var(--stage);
    font-family: "Lato", Arial, sans-serif;
  }
  .page-label {
    position: absolute; top: 45px; left: 0; width: 1200px;
    text-align: center; color: var(--white);
    font-weight: 300; font-size: 25px; letter-spacing: 0.5px;
  }
  .slide {
    position: absolute; left: 68px; top: 106px;
    width: 1328px; height: 996px;
    transform: scale(0.8); transform-origin: top left;
    background: radial-gradient(ellipse at 55% 35%, #ffffff 0%, #f6f6f6 55%, #ececec 100%);
    overflow: hidden;
  }
  .slide-frame { position: absolute; inset: 0; }
  .slide-title {
    position: absolute; left: 40px; top: 86px;
    color: var(--white); font-weight: 300; font-size: 50px; line-height: 60px;
  }
  .brand-name {
    position: absolute; left: 1085px; top: 90px;
    display: flex; align-items: center; gap: 14px;
    color: var(--white); font-weight: 700; font-size: 34px; line-height: 50px;
  }
  .brand-name .brand-dot {
    width: 20px; height: 20px; background: var(--orange);
  }
  .image-slot {
    position: absolute; left: 80px; top: 255px; width: 545px; height: 342px;
    background: var(--placeholder);
    display: flex; align-items: center; justify-content: center;
    color: rgba(255,255,255,0.75); font-weight: 300; font-size: 40px;
  }
  .intro-copy {
    position: absolute; left: 80px; top: 647px; width: 553px;
    color: var(--body-text); font-size: 25px; line-height: 31px;
    text-align: justify;
  }
  .point-list {
    position: absolute; left: 713px; top: 297px; width: 560px;
    list-style: none;
  }
  .point-list li {
    position: relative; padding-left: 35px; margin-bottom: 40px;
    color: var(--body-text); font-size: 26px; line-height: 40px;
  }
  .point-list li::before {
    content: ""; position: absolute; left: 0; top: 13px;
    width: 14px; height: 14px; background: var(--orange);
  }
  .footer-text {
    position: absolute; left: 36px; top: 949px;
    color: var(--white); font-size: 18px; line-height: 26px;
  }
  .footer-text .divider { margin: 0 8px; }
</style>
</head>
<body>
  <div class="page-label">Page 4</div>

  <section class="slide">
    <svg class="slide-frame" width="1328" height="996" viewBox="0 0 1328 996" aria-hidden="true">
      <defs>
        <linearGradient id="bandGrad" x1="0" y1="0" x2="1" y2="0">
          <stop offset="0" stop-color="#e67e17"/>
          <stop offset="0.6" stop-color="#ea8519"/>
          <stop offset="1" stop-color="#f0931f"/>
        </linearGradient>
      </defs>
      <!-- header band -->
      <polygon points="0,62 1012,62 905,167 0,167" fill="url(#bandGrad)"/>
      <polygon points="0,145 920,145 900,167 0,167" fill="#f0961f" opacity="0.8"/>
      <polygon points="800,62 1012,62 905,167 720,167" fill="#f29a22" opacity="0.35"/>
      <!-- black brand block -->
      <polygon points="1018,62 1328,62 1328,167 910,167" fill="var(--black)"/>
      <!-- thin accent above -->
      <polygon points="1034,44 1328,44 1328,57 1021,57" fill="var(--orange-deep)"/>
      <!-- black rule under header -->
      <polygon points="0,172 896,172 882,185 0,185" fill="var(--black)"/>
      <!-- footer -->
      <polygon points="0,943 380,943 340,982 0,982" fill="var(--black)"/>
      <polygon points="388,943 1328,943 1328,982 348,982" fill="var(--orange-deep)"/>
    </svg>

    <h1 class="slide-title">Title Goes Here</h1>
    <div class="brand-name"><span class="brand-dot"></span>Bold Ledger</div>

    <div class="image-slot" role="img" aria-label="Image placeholder for slide visual">Image Goes Here</div>

    <p class="intro-copy">Duis autem vel eum iriure dolor in hendrerit in vulputate velit esse molestie consequat, vel illum dolore eu feugiat nulla facilisis at vero eros et accumsan et iusto odio dignissim qui blandit praesent luptatum zzril delenit augue duis dolore te feugait nulla facilisi.</p>

    <ul class="point-list">
      <li>Souvlaki ignitus carborundum e pluribus unum.</li>
      <li>Defacto lingo est igpay atinlay. Marquee selectus non provisio.</li>
      <li>Quote meon an estimate et non interruptus stadium.</li>
      <li>Sic tempus fugit esperanto hiccup estrogen.</li>
      <li>Epsum factorial non deposit quid pro quo hic escorol.</li>
    </ul>

    <div class="footer-text">www.boldledger.com<span class="divider">|</span>Page 2</div>
  </section>
</body>
</html>
```